New Business Card Design Project LORVANTI-Italy

we are LORVANTI-Italy
our company in the market for 3 years we are luxury cosmetic company and its about time for a facelift :)
i will like to have elegant luxurious and unique business card
that will give the person that get it a unique, luxurious and elegant impression
I'm VERY OPEN FOR NEW IDEAS , even duo i add a few files of things that i see on line and i like them

i add my logo as well
my website is LORVANTI.COM
(if you would like to see the main style that we have)

Target Market(s)

adult that have money :)

Industry/Entity Type

Business

Contact Information for Business Card

Name - Dario Lorvanti
Position - CEO and CO Founder
address - 4817 E Halvern
telephone - 555-384-1926
email - dario@lorvanti.com
fax - 555-384-1926
website - LORVANTI.COM

Colors
000000
959595
fbee3e
ffffff

Requirements
Must have
• big logo in GOLD color
• elegant look
• impressive
Nice to have
• not must but maybe classy pattern background
• not must but maybe emblem
• maybe clear plastic business card
Should not have
• colors
• images

```html
<!DOCTYPE html>
<html lang="en">
<head>
<meta charset="utf-8">
<title>LORVANTI Italy – Business Card</title>
<link rel="stylesheet" href="https://fonts.googleapis.com/css2?family=Cinzel:wght@500&family=Roboto:wght@400;700&display=swap">
<style>
  :root {
    --backdrop: #2e2825;
    --card: #16181a;
    --gold: #d9a928;
    --gold-light: #f0c94a;
    --white: #f4f4f4;
    --grey: #959595;
  }
  * { box-sizing: border-box; margin: 0; padding: 0; }
  html, body { width: 1200px; height: 769px; overflow: hidden; }
  body {
    background: var(--backdrop);
    font-family: "Roboto", Arial, sans-serif;
    position: relative;
  }
  .card {
    position: absolute;
    top: 88px;
    width: 340px;
    height: 594px;
    background: var(--card);
    border-radius: 3px;
    box-shadow: 0 14px 30px rgba(0,0,0,.45);
  }
  .card--front { left: 220px; }
  .card--back  { left: 640px; }

  /* front */
  .brand-seal {
    position: absolute;
    left: 50%;
    top: 90px;
    width: 240px;
    height: 240px;
    margin-left: -120px;
    border: 3px solid var(--gold);
    border-radius: 50%;
    display: flex;
    align-items: center;
    justify-content: center;
  }
  .brand-name {
    font-family: "Cinzel", Georgia, serif;
    font-weight: 500;
    color: var(--gold);
    letter-spacing: 2px;
  }
  .brand-seal .brand-name { font-size: 30px; }
  .holder {
    position: absolute;
    left: 44px;
    bottom: 70px;
  }
  .holder__name {
    font-weight: 700;
    font-size: 24px;
    color: var(--gold);
    letter-spacing: .5px;
    padding-bottom: 8px;
    border-bottom: 2px solid var(--gold);
  }
  .holder__role {
    margin-top: 10px;
    font-size: 15px;
    color: var(--white);
  }

  /* back */
  .lockup {
    position: absolute;
    left: 44px;
    right: 44px;
    top: 70px;
  }
  .lockup__row {
    display: flex;
    align-items: center;
    justify-content: space-between;
    padding-bottom: 10px;
    border-bottom: 2px solid var(--gold);
  }
  .lockup .brand-name { font-size: 36px; }
  .lockup__dot {
    width: 56px;
    height: 56px;
    border: 2px solid var(--gold);
    border-radius: 50%;
    flex: none;
  }
  .lockup__country {
    margin-top: 8px;
    font-family: "Cinzel", Georgia, serif;
    font-size: 13px;
    letter-spacing: 3px;
    color: var(--gold);
  }
  .contact {
    position: absolute;
    left: 44px;
    top: 300px;
    list-style: none;
    font-size: 14px;
    line-height: 1.75;
    color: var(--white);
    letter-spacing: .3px;
  }
  .contact__label { color: var(--gold); font-weight: 700; }
  .contact__web { color: var(--gold); }
</style>
</head>
<body>
  <section class="card card--front" aria-label="Business card front">
    <div class="brand-seal">
      <span class="brand-name">LORVANTI</span>
    </div>
    <div class="holder">
      <p class="holder__name">DARIO LORVANTI</p>
      <p class="holder__role">CEO &amp; CO Founder</p>
    </div>
  </section>

  <section class="card card--back" aria-label="Business card back">
    <div class="lockup">
      <div class="lockup__row">
        <span class="brand-name">LORVANTI</span>
        <span class="lockup__dot"></span>
      </div>
      <p class="lockup__country">ITALY</p>
    </div>
    <ul class="contact">
      <li>4817 E HALVERN</li>
      <li><span class="contact__label">P:</span> 555-384-1926</li>
      <li><span class="contact__label">F:</span> 555-384-1926</li>
      <li>DARIO@LORVANTI.COM</li>
      <li class="contact__web">WWW.LORVANTI.COM</li>
    </ul>
  </section>
</body>
</html>
```